Varnik Holdings — Business Card Design Brief
Overview
Design a double-sided business card for Varnik Holdings that highlights our two service arms: Varnik Communications (telecommunications) and Varnik Energy (business energy solutions). The card should feel smart and stand out when handed to clients.

Objectives
Showcase our areas of specialty clearly.
Reflect the overall Varnik / Varnik Holdings brand while acknowledging both arms.
Explore using both logos (Communications + Energy) or one unified logo, depending on the design.

Deliverables
One double-sided business card design (front + back).

Content & Copy
Front (preferred): Logo: Varnik / Varnik Holdings
Descriptor: Business Communications | Business Energy
Back:My contact details and company details
Core products: Business Mobile • Telephony • Internet • Business Energy Solutions

Brand & Visual Direction
We have a group logo currently tailored more toward telecoms, plus a separate Varnik Energy logo.
Please explore layouts that use both logos or just one, whichever works best.
Color: I wouldn't mind seeing an option using our the Blue/Purple gradient from our website (varnik-example.co.uk), but also open to non-gradient approaches and other colours..

Overall look: Smart, modern, and distinctive.
Format & Print Specs
Double-sided business card format. (Use a standard size

Must-Haves
Front: Varnik wording or Varnik Holdings wording with atleast 1 logo also on front “Business Communications | Business Energy.”

Back: Contact + company details and core products.
A design that stands out while remaining professional.

Nice-to-Have Options
A gradient version using our site’s Blue/Purple gradient.
A non-gradient version.
A dual-logo treatment versus a single-logo treatment.

Thanks
Owen

```html
<!DOCTYPE html>
<html lang="en">
<head>
<meta charset="utf-8">
<title>Varnik Holdings — Business Card</title>
<link href="https://fonts.googleapis.com/css2?family=Open+Sans:wght@400;600;800&display=swap" rel="stylesheet">
<style>
  :root {
    --bg: #2e2f31;
    --card: #ffffff;
    --card-shade: #e9e9eb;
    --navy: #1f1d5c;
    --text: #3c3c4a;
    --muted: #6a6a78;
    --green: #5cb335;
    --rule: #8a8aa8;
    --band-start: #7a3c96;
    --band-end: #4454a8;
    --brand-dot: #3a8fd0;
  }
  * { box-sizing: border-box; margin: 0; padding: 0; }
  html, body { width: 1200px; height: 900px; overflow: hidden; }
  body {
    background: var(--bg);
    font-family: "Open Sans", Arial, sans-serif;
    position: relative;
  }
  .card {
    position: absolute;
    width: 560px;
    height: 320px;
    background: linear-gradient(120deg, var(--card-shade) 0%, var(--card) 55%, var(--card) 100%);
    box-shadow: 0 12px 30px rgba(0,0,0,.45);
    overflow: hidden;
  }
  .card--front { left: 70px; top: 70px; }
  .card--back { left: 570px; top: 510px; }
  .card__band {
    position: absolute; left: 0; right: 0; bottom: 0; height: 30px;
    background: linear-gradient(90deg, var(--band-start), var(--band-end));
  }
  .brand { display: flex; align-items: center; gap: 12px; }
  .brand__dot {
    width: 34px; height: 34px; border-radius: 50%;
    background: var(--brand-dot);
  }
  .brand__name {
    font-weight: 800; color: var(--navy); letter-spacing: 1px; font-size: 40px; line-height: 1;
  }
  .card--front .brand { position: absolute; right: 40px; top: 36px; }
  .products {
    position: absolute; right: 40px; top: 88px;
    font-size: 11px; font-weight: 600; color: var(--muted); white-space: nowrap;
  }

  .brand-block {
    position: absolute; left: 50%; top: 44%; transform: translate(-50%, -50%);
    display: flex; flex-direction: column; align-items: center; gap: 12px;
  }
  .card--back .brand__name { font-size: 52px; }
  .card--back .brand__dot { width: 44px; height: 44px; }
  .descriptor {
    font-size: 14px; font-weight: 600; color: var(--muted); letter-spacing: .5px; white-space: nowrap;
  }
  .descriptor__sep { color: var(--band-end); margin: 0 6px; }

  .person { position: absolute; left: 34px; top: 140px; }
  .person__name { font-weight: 800; font-size: 15px; color: var(--navy); letter-spacing: .5px; }
  .person__role { font-size: 13px; color: var(--muted); }

  .contacts {
    position: absolute; left: 34px; top: 192px; right: 40px;
    font-size: 13.5px; color: var(--text);
  }
  .contacts__row { display: flex; align-items: stretch; }
  .contacts__group { display: flex; flex-direction: column; gap: 4px; }
  .contacts__group--web {
    border-left: 1px solid var(--rule); padding-left: 14px; margin-left: 18px;
  }
  .contact { display: flex; align-items: center; gap: 8px; white-space: nowrap; }
  .contact svg { width: 14px; height: 14px; flex: none; }
  .contacts__rule { border-top: 1px solid var(--rule); margin: 8px 0 6px; width: 420px; }
</style>
</head>
<body>

<section class="card card--front" aria-label="Business card, contact side">
  <div class="brand">
    <span class="brand__dot"></span>
    <span class="brand__name">VARNIK</span>
  </div>
  <p class="products">Business Mobile • Telephony • Internet • Business Energy Solutions</p>

  <div class="person">
    <p class="person__name">DANIEL HART</p>
    <p class="person__role">Director</p>
  </div>

  <div class="contacts">
    <div class="contacts__row">
      <div class="contacts__group">
        <p class="contact">
          <svg viewBox="0 0 14 14"><rect x="3.5" y="1" width="7" height="12" rx="1.2" fill="none" stroke="var(--green)" stroke-width="1.3"/><line x1="6" y1="11" x2="8" y2="11" stroke="var(--green)" stroke-width="1.2"/></svg>
          +44 7700 900 123
        </p>
        <p class="contact">
          <svg viewBox="0 0 14 14"><path d="M3 1.5l2 2.6-1.2 1.4c.8 1.7 2 2.9 3.7 3.7l1.4-1.2 2.6 2-1 2C6.5 12 2 7.5 1 2.5z" fill="var(--green)"/></svg>
          +44 0161 496 0017
        </p>
      </div>
      <div class="contacts__group contacts__group--web">
        <p class="contact">
          <svg viewBox="0 0 14 14"><rect x="1" y="3" width="12" height="8" fill="var(--green)"/><path d="M1 3l6 4.5L13 3" fill="none" stroke="#fff" stroke-width="1.1"/></svg>
          info@varnik-example.co.uk
        </p>
        <p class="contact">
          <svg viewBox="0 0 14 14" fill="none" stroke="var(--green)" stroke-width="1.1"><circle cx="7" cy="7" r="5.8"/><ellipse cx="7" cy="7" rx="2.6" ry="5.8"/><line x1="1.2" y1="7" x2="12.8" y2="7"/></svg>
          www.varnik-example.co.uk
        </p>
      </div>
    </div>
    <div class="contacts__rule"></div>
    <p class="contact">
      <svg viewBox="0 0 14 14"><path d="M7 13s-4.5-5-4.5-7.8a4.5 4.5 0 019 0C11.5 8 7 13 7 13z" fill="var(--green)"/><circle cx="7" cy="5.3" r="1.6" fill="#fff"/></svg>
      24 Example Row, Manchester, England, M1 0AA
    </p>
  </div>

  <div class="card__band"></div>
</section>

<section class="card card--back" aria-label="Business card, brand side">
  <div class="brand-block">
    <div class="brand">
      <span class="brand__dot"></span>
      <span class="brand__name">VARNIK</span>
    </div>
    <p class="descriptor">Business Communications<span class="descriptor__sep">|</span>Business Energy</p>
  </div>
  <div class="card__band"></div>
</section>

</body>
</html>
```